Need Business Card for our Real Estate Business with Sales Executive's Picture

PANTONE 484 C ( RED)

PANTONE 2766 C ( BLUE

Industry/Entity Type

Real Estate

Contact Information for Business Card

Name, Mobile, email, & picture of Person
Agency Phone, address, Web address

Requirements
Must have
• Our Logo Colours, Agent Picture,

```html
<!DOCTYPE html>
<html lang="en">
<head>
<meta charset="utf-8">
<title>Harbor Lane Homes – Business Card</title>
<link rel="stylesheet" href="https://fonts.googleapis.com/css2?family=Amaranth:wght@700&family=Open+Sans:wght@400;600&display=swap">
<style>
  :root {
    --brand-red: #9a3324;
    --brand-navy: #141b4d;
    --card-surface: #eef0ef;
    --page-bg: #d8d4ce;
    --text-navy: #1f2a5c;
    --photo-light: #d9cfc4;
    --photo-dark: #a99a8b;
  }
  * { margin: 0; padding: 0; box-sizing: border-box; }
  html, body {
    width: 1200px; height: 1054px; overflow: hidden;
    background: var(--page-bg);
  }
  .business-card {
    position: absolute;
    left: 100px; top: 225px;
    width: 1000px; height: 603px;
    background: var(--card-surface);
    box-shadow: 0 10px 30px rgba(0,0,0,0.18);
    overflow: hidden;
    font-family: "Open Sans", sans-serif;
    color: var(--text-navy);
  }
  .agent-name {
    position: absolute; left: 62px; top: 84px;
    font-family: "Amaranth", sans-serif; font-weight: 700;
    font-size: 32px; color: var(--brand-red); line-height: 1.1;
  }
  .agent-title {
    position: absolute; left: 62px; top: 124px;
    font-size: 23px; line-height: 1.2;
  }
  .office-address {
    position: absolute; left: 62px; top: 310px;
    font-size: 24px; line-height: 37px; font-style: normal;
  }
  .contact-list {
    position: absolute; left: 62px; top: 396px;
    list-style: none;
  }
  .contact-item {
    display: flex; align-items: center;
    height: 33px; font-size: 24px;
  }
  .contact-icon {
    width: 20px; height: 20px; margin: 0 22px 0 2px;
    fill: var(--brand-red);
  }
  .web-domain { color: var(--brand-red); }
  .agent-photo {
    position: absolute; left: 700px; top: 60px;
    width: 230px; height: 290px;
    background: linear-gradient(160deg, var(--photo-light), var(--photo-dark));
    border-bottom: 6px solid var(--brand-red);
  }
  .brand-band {
    position: absolute; left: 0; bottom: 0;
  }
  .brand-lockup {
    position: absolute; left: 600px; top: 440px;
    width: 380px;
    display: flex; align-items: center; gap: 16px;
  }
  .brand-square {
    width: 36px; height: 36px; flex: none;
    background: var(--brand-red);
  }
  .brand-name {
    font-family: "Open Sans", sans-serif; font-weight: 600;
    font-size: 32px; line-height: 1.1; color: var(--brand-navy);
    white-space: nowrap;
  }
</style>
</head>
<body>
  <article class="business-card">
    <h1 class="agent-name">Maren Whitfield</h1>
    <p class="agent-title">Managing Director</p>

    <div class="agent-photo" role="img" aria-label="Portrait photo of the sales executive"></div>

    <address class="office-address">418 Cedar Row #2210,<br>Brookfield, CO 80990</address>

    <ul class="contact-list">
      <li class="contact-item">
        <svg class="contact-icon" viewBox="0 0 20 20" aria-hidden="true"><rect x="4" y="1" width="12" height="18" rx="2"/><rect x="6" y="4" width="8" height="10" fill="#eef0ef"/><circle cx="10" cy="16.5" r="1.1" fill="#eef0ef"/></svg>
        555.201.3348
      </li>
      <li class="contact-item">
        <svg class="contact-icon" viewBox="0 0 20 20" aria-hidden="true"><path d="M1 7c0-3 4-4 9-4s9 1 9 4v2h-4V7H5v2H1z"/><path d="M4 10h12l2 8H2z"/><circle cx="10" cy="14" r="2" fill="#eef0ef"/></svg>
        555-201-7790
      </li>
      <li class="contact-item">
        <svg class="contact-icon" viewBox="0 0 20 20" aria-hidden="true"><rect x="1" y="4" width="18" height="12"/><path d="M1 4l9 7 9-7" fill="none" stroke="#eef0ef" stroke-width="1.6"/></svg>
        mwhitfield@harborlanehomes.com
      </li>
      <li class="contact-item">
        <svg class="contact-icon" viewBox="0 0 20 20" aria-hidden="true"><circle cx="10" cy="10" r="8.5"/><g fill="none" stroke="#eef0ef" stroke-width="1.2"><ellipse cx="10" cy="10" rx="3.5" ry="8.5"/><path d="M1.5 10h17M3 6h14M3 14h14"/></g></svg>
        <span>www.<span class="web-domain">harborlanehomes</span>.com</span>
      </li>
    </ul>

    <svg class="brand-band" width="1000" height="70" viewBox="0 0 1000 70" aria-hidden="true">
      <polygon points="0,70 0,66 560,20 1000,20 1000,70" fill="var(--brand-navy)"/>
    </svg>

    <div class="brand-lockup">
      <span class="brand-square" aria-hidden="true"></span>
      <span class="brand-name">Harbor Lane Homes</span>
    </div>
  </article>
</body>
</html>
```